RV7 - Rapid Vigil Field Operations Suite

I need an introductory website for RV7 which describes the features of the product and the ease of use of the product. The product is focused on Preparing for an incident using Volunteer and Resource management and then responding to an incident with Incident Management, Team Management, Task Management and Communication Management. Once a situation is handled, the application provides complete reporting on each of the above aspects

Target Market(s)

Local Government entities, specifically the emergency department directors or coordinators

Industry/Entity Type

Government Office

Coding

Coded - Design and coding required

Font styles to use
Sans Serif

Requirements
Must have
• Clear layout with modern images. I want to be able to get a clear understanding of the features of the product and the ease of use. I would like to high light how the application helps in Communication Management, Team Management, Task Management and Incident Managements. Also, how the use of application helps to get an immediate snap shot of how well an incident was handled. I want to highlight how the Dashboard provides a quick look at the Incident(s) being managed
Nice to have
• I would like to in the future add videos to the site. At this point don't have any ideas about nice to have features
Should not have
• traditional designs. I am looking for a slick, modern looking website. Clean design is the key.

```html
<!DOCTYPE html>
<html lang="en">
<head>
<meta charset="utf-8">
<title>RV7 - Rapid Vigil Field Operations Suite</title>
<link href="https://fonts.googleapis.com/css2?family=Open+Sans:wght@400;600;700&family=Source+Sans+3:wght@400;600&display=swap" rel="stylesheet">
<style>
:root{
  --blue:#2a5ea8;
  --blue-dark:#214f91;
  --green:#8cbb2b;
  --green-dark:#76a31f;
  --page:#ececec;
  --page-light:#f1f1f1;
  --ink:#222;
  --text:#5a5a5a;
  --line:#d6d6d6;
  --white:#fff;
}
*{margin:0;padding:0;box-sizing:border-box}
html,body{width:1200px;height:2206px;overflow:hidden}
body{position:relative;background:var(--page);font-family:"Open Sans",sans-serif;color:var(--text)}
.abs{position:absolute}
.heading{font-family:"Source Sans 3",sans-serif;font-weight:400;color:var(--ink)}

/* header */
.site-header{left:0;top:0;width:1200px;height:122px;background:var(--white)}
.brand{left:110px;top:26px;display:flex;align-items:center;gap:14px}
.brand-mark{width:62px;height:70px;border:4px solid var(--blue);border-radius:6px}
.brand-name{font-family:"Source Sans 3",sans-serif;font-size:32px;font-weight:600;color:var(--ink);line-height:1}
.brand-tag{font-size:11px;color:var(--ink);margin-top:6px;line-height:1.4}
.nav a{position:absolute;top:0;height:122px;line-height:128px;font-size:13px;font-weight:600;color:var(--ink);text-decoration:none}
.nav .active{left:541px;width:100px;text-align:center;color:var(--blue);border-left:1px solid #e2e2e2;border-right:1px solid #e2e2e2;box-shadow:0 0 6px rgba(0,0,0,.12);border-bottom:4px solid var(--blue);height:122px}

/* hero */
.hero{left:0;top:122px;width:1200px;height:471px;background:linear-gradient(100deg,#2d3236 0%,#4b5358 35%,#6b7378 60%,#3a4046 100%);border-bottom:2px solid var(--green)}
.hero-title{left:110px;top:388px;font-size:40px;color:var(--white);letter-spacing:.5px}
.hero-text{left:112px;top:448px;width:460px;font-size:12px;line-height:25px;color:#eee}
.dots{left:567px;top:558px;display:flex;gap:10px}
.dots span{width:9px;height:9px;border-radius:50%;background:#3d4347}
.dots .on{background:var(--green)}

/* welcome */
.welcome{left:0;top:595px;width:1200px;height:287px;background:linear-gradient(#f1f1f1,#e4e4e4)}
.device{left:179px;top:654px;width:186px;height:228px;border-radius:22px 22px 0 0;background:linear-gradient(#222 0 18%,#1f4fb8 18%,#2356c8 100%);border:8px solid #1b1b1b;border-bottom:none}
.welcome-title{left:444px;top:675px;font-size:33px}
.welcome-title span{color:var(--blue)}
.welcome-text{left:445px;top:733px;width:640px;font-size:11.5px;line-height:26px}

/* features */
.features{left:0;top:882px;width:1200px;height:412px;background:var(--page-light)}
.feature{top:963px;width:250px;text-align:center}
.feature svg{display:block;margin:0 auto}
.feature h3{font-family:"Source Sans 3",sans-serif;font-weight:400;font-size:17px;color:var(--ink);margin-top:22px;letter-spacing:.3px}
.feature p{font-size:11.5px;line-height:25px;margin-top:10px}
.feature a{display:inline-block;margin-top:6px;font-size:12px;color:var(--green);text-decoration:none}

/* newsletter */
.newsletter{left:0;top:1294px;width:1200px;height:360px;background:var(--blue);text-align:center}
.newsletter h2{margin-top:70px;font-family:"Source Sans 3",sans-serif;font-weight:400;font-size:31px;color:var(--white);letter-spacing:.5px}
.newsletter p{width:940px;margin:22px auto 0;font-size:11.5px;line-height:27px;color:var(--white)}
.email-field{left:298px;top:1516px;width:356px;height:50px;background:var(--white);border-bottom:3px solid #d9d9d9;font-size:11.5px;padding-left:22px;line-height:50px;text-align:left}
.subscribe{left:684px;top:1515px;width:218px;height:54px;background:linear-gradient(var(--green),var(--green-dark));color:var(--white);font-weight:700;font-size:15px;line-height:54px;letter-spacing:.5px}

/* footer */
.footer{left:0;top:1654px;width:1200px;height:441px;background:var(--page)}
.col-title{top:1712px;font-size:25px}
.about-box{left:112px;top:1777px;width:302px;height:138px;background:linear-gradient(#fff,#ececec);border:1px solid #ddd;display:flex;align-items:center;justify-content:center;gap:14px}
.about-box .brand-mark{width:56px;height:64px}
.about-text{left:112px;top:1942px;width:300px;font-size:11.5px;line-height:26px}
.contact-item{left:469px;width:242px;display:flex;align-items:center;gap:20px;font-size:11.5px;line-height:25px}
.contact-icon{flex:none;width:52px;height:52px;border-radius:50%;background:var(--green);display:flex;align-items:center;justify-content:center}
.rule{left:530px;width:182px;height:1px;background:var(--line)}
.field{left:764px;width:316px;background:var(--white);border:1px solid #d8d8d8;font-size:11px;padding:14px 18px;color:#888}
.submit{left:764px;top:1998px;width:316px;height:46px;background:linear-gradient(var(--green),var(--green-dark));color:var(--white);font-weight:700;font-size:14px;text-align:center;line-height:46px}

/* bottom */
.bottom-bar{left:0;top:2095px;width:1200px;height:111px;background:var(--blue)}
.copyright{left:110px;top:2140px;font-size:12px;color:var(--white)}
.social{left:965px;top:2136px;display:flex;gap:6px}
.social span{width:26px;height:26px;border-radius:50%;background:#3f74c1;border:1px solid #5d8ad0}
</style>
</head>
<body>

<header class="abs site-header">
  <div class="abs brand">
    <div class="brand-mark"></div>
    <div>
      <div class="brand-name">RV7</div>
      <div class="brand-tag">Rapid Vigil Field<br>Operations Suite</div>
    </div>
  </div>
  <nav class="nav">
    <a class="active" href="#">HOME</a>
    <a style="left:671px" href="#">ABOUT US</a>
    <a style="left:795px" href="#">SERVICES</a>
    <a style="left:912px" href="#">NEWS</a>
    <a style="left:1008px" href="#">CONTACT US</a>
  </nav>
</header>

<section class="abs hero" role="img" aria-label="Photo of hands using a smartphone in an office"></section>
<h1 class="abs heading hero-title">RESOURCE MANAGEMENT</h1>
<p class="abs hero-text">Lorem ipsum dolor sit amet, consectetur adipiscing elit. Integer sed velit malesuada, dapibus sapien ac, eleifend arcu.</p>
<div class="abs dots"><span></span><span></span><span class="on"></span><span></span></div>

<section class="abs welcome"></section>
<div class="abs device" role="img" aria-label="Smartphone showing the RV7 volunteer app menu"></div>
<h2 class="abs heading welcome-title">WELCOME TO <span>RV7</span></h2>
<p class="abs welcome-text">Duis lobortis, risus et blandit vehicula, quam augue facilisis enim, sed condimentum lectus nulla in sem. Nunc aliquam non dolor a pulvinar. Donec at eros malesuada, efficitur risus eu, vulputate ante. Vivamus tincidunt felis eu cursus hendrerit. Phasellus tincidunt venenatis quam vitae euismod. Sed commodo sodales justo, a vestibulum odio tincidunt et. Duis rhonc us tempor sagittis. Duis id vestibulum sem. Morbi dignissim dolor est, eget rhoncus sem interdum vitae.</p>

<section class="abs features"></section>

<div class="abs feature" style="left:98px">
  <svg width="106" height="126" viewBox="0 0 72 86"><path d="M36 0 44 6Q56 12 72 10V46Q72 70 36 86 0 70 0 46V10Q16 12 28 6Z" fill="#2a5ea8"/><circle cx="34" cy="40" r="8" fill="none" stroke="#fff" stroke-width="3.5"/><path d="M40 46 47 53" stroke="#fff" stroke-width="4" stroke-linecap="round"/></svg>
  <h3>INCIDENT MANAGEMENT</h3>
  <p>Vivamus eleifend nulla tristique risus<br>condimentum, vel finibus enim.</p>
  <a href="#">» READ MORE</a>
</div>
<div class="abs feature" style="left:348px">
  <svg width="106" height="126" viewBox="0 0 72 86"><path d="M36 0 44 6Q56 12 72 10V46Q72 70 36 86 0 70 0 46V10Q16 12 28 6Z" fill="#2a5ea8"/><g fill="#fff"><circle cx="36" cy="34" r="5"/><circle cx="26" cy="37" r="4"/><circle cx="46" cy="37" r="4"/><path d="M27 52Q27 42 36 42 45 42 45 52Z"/><path d="M18 51Q18 43 26 43 29 43 30 44 25 47 25 51Z"/><path d="M54 51Q54 43 46 43 43 43 42 44 47 47 47 51Z"/></g></svg>
  <h3>VOLUNTEER MANAGEMENT</h3>
  <p>Vivamus eleifend nulla tristique risus<br>condimentum, vel finibus enim.</p>
  <a href="#">» READ MORE</a>
</div>
<div class="abs feature" style="left:600px">
  <svg width="106" height="126" viewBox="0 0 72 86"><path d="M36 0 44 6Q56 12 72 10V46Q72 70 36 86 0 70 0 46V10Q16 12 28 6Z" fill="#2a5ea8"/><g fill="none" stroke="#fff" stroke-width="2.5" stroke-linejoin="round"><path d="M36 28 44 32 36 36 28 32Z M28 32V40L36 44 44 40V32 M36 36V44"/><path d="M28 42 20 46V54L28 58 36 54 44 58 52 54V46L44 42 M20 46 28 50 36 46 44 50 52 46 M28 50V58 M44 50V58 M36 46V54"/></g></svg>
  <h3>DAMAGE ASSESSMENT</h3>
  <p>Vivamus eleifend nulla tristique risus<br>condimentum, vel finibus enim.</p>
  <a href="#">» READ MORE</a>
</div>
<div class="abs feature" style="left:850px">
  <svg width="106" height="126" viewBox="0 0 72 86"><path d="M36 0 44 6Q56 12 72 10V46Q72 70 36 86 0 70 0 46V10Q16 12 28 6Z" fill="#2a5ea8"/><g fill="#fff"><path d="M22 36H30L46 28V54L30 46H22Z"/><path d="M26 46H32L34 56H29Z"/><rect x="48" y="37" width="5" height="8" rx="2"/></g></svg>
  <h3>TASK MANAGEMENT</h3>
  <p>Vivamus eleifend nulla tristique risus<br>condimentum, vel finibus enim.</p>
  <a href="#">» READ MORE</a>
</div>

<section class="abs newsletter">
  <h2>SIGNUP OUR NEWSLETTER</h2>
  <p>Phasellus tincidunt venenatis quam vitae euismod. Sed commodo sodales justo, a vestibulum odio tincidunt et. Duis rhonc us tempor sagittis. Duis id vestibulum sem. Morbi dignis-sim dolor est, eget rhoncus sem interdum vitae.</p>
</section>
<div class="abs email-field">Email Address</div>
<div class="abs subscribe" style="text-align:center">SUBSCRIBE</div>

<footer class="abs footer"></footer>
<h3 class="abs heading col-title" style="left:110px">ABOUT US</h3>
<h3 class="abs heading col-title" style="left:459px">CONTACT</h3>
<h3 class="abs heading col-title" style="left:762px">SEND MAIL</h3>

<div class="abs about-box">
  <div class="brand-mark"></div>
  <div>
    <div class="brand-name">RV7</div>
    <div class="brand-tag">Rapid Vigil Field<br>Operations Suite</div>
  </div>
</div>
<p class="abs about-text">Donec at eros malesuada, efficitur risus eu, vulputate ante. Vivamus tincidunt felis eu cursus hendrerit. Phase llus tincidunt venenatis quam vitae euismod. Sed comm odo sodales justo, a vestibulum odio tincidunt.</p>

<div class="abs contact-item" style="top:1778px">
  <div class="contact-icon"><svg width="14" height="18" viewBox="0 0 14 18"><path d="M7 0A7 7 0 0 0 0 7C0 12 7 18 7 18S14 12 14 7A7 7 0 0 0 7 0Z" fill="#fff"/><circle cx="7" cy="7" r="2.5" fill="#8cbb2b"/></svg></div>
  <div>123,Lorem Ipsm, Lorem Ipsm,<br>Lorem Ipsm - 123 456</div>
</div>
<div class="abs rule" style="top:1852px"></div>
<div class="abs contact-item" style="top:1869px">
  <div class="contact-icon"><svg width="16" height="16" viewBox="0 0 16 16"><path d="M3 0 6 4 4 6Q6 10 10 12L12 10 16 13 14 16Q4 15 0 3Z" fill="#fff"/></svg></div>
  <div>(000) 987 654 321 000</div>
</div>
<div class="abs rule" style="top:1941px"></div>
<div class="abs contact-item" style="top:1959px">
  <div class="contact-icon"><svg width="18" height="13" viewBox="0 0 18 13"><rect width="18" height="13" rx="1.5" fill="#fff"/><path d="M1 1 9 7 17 1" fill="none" stroke="#8cbb2b" stroke-width="1.5"/></svg></div>
  <div>info@rv7-suite.example</div>
</div>

<div class="abs field" style="top:1779px;height:45px">Name</div>
<div class="abs field" style="top:1839px;height:45px">Email Address</div>
<div class="abs field" style="top:1896px;height:86px">Message</div>
<div class="abs submit">SUBMIT</div>

<div class="abs bottom-bar"></div>
<p class="abs copyright">Copyrights © 2016 RV7. All Right Reserved.</p>
<div class="abs social" aria-label="Social links"><span></span><span></span><span></span><span></span></div>

</body>
</html>
```